Thornvale Group needs a business card design

We need a new business card design using the logo recently selected in a logo competition on Pixel Bazaar. Our business is a consultancy specializing in aviation and energy and the winning business card design will promote an image of precision and professionalism with creativity.

Please use the logo with the name on the front of the card and use a complementary font. Make the back white with either the light grey or dark grey logo.

Target Market(s)

Senior finance and legal leaders at aviation and energy companies

Industry/Entity Type

Management Consulting

Contact Information for Business Card

Peter Castrell
President
Thornvale Group

www.thornvalegroup.example

(555) 204-6391
pc@thornvalegroup.example

Requirements
Must have
• Professional font that goes well with the logo font

```html
<!DOCTYPE html>
<html lang="en">
<head>
<meta charset="utf-8">
<title>Thornvale Group – Business Card</title>
<link href="https://fonts.googleapis.com/css2?family=Open+Sans:wght@300;400;700&display=swap" rel="stylesheet">
<style>
  :root {
    --page: #e9e7e3;
    --navy: #0d3a66;
    --navy-deep: #0a2d52;
    --steel: #2e80a9;
    --white: #ffffff;
    --grey-band: #6d7075;
    --ink: #1f4f7a;
    --soft-white: rgba(255,255,255,0.9);
  }
  html, body {
    margin: 0;
    width: 1200px;
    height: 913px;
    overflow: hidden;
    background: var(--page);
    font-family: "Open Sans", Arial, sans-serif;
  }
  .canvas {
    position: relative;
    width: 1200px;
    height: 913px;
  }
  .card {
    position: absolute;
    top: 302px;
    width: 540px;
    height: 309px;
    overflow: hidden;
    box-shadow: 0 6px 18px rgba(0,0,0,0.18);
  }
  .card-front {
    left: 40px;
    background: linear-gradient(160deg, var(--steel) 0%, var(--navy) 60%, var(--navy-deep) 100%);
    color: var(--white);
  }
  .card-back {
    left: 620px;
    background: var(--white);
  }
  .card-bands {
    position: absolute;
    inset: 0;
  }
  .brand-name {
    position: absolute;
    font-weight: 300;
    letter-spacing: 2px;
    text-transform: uppercase;
    white-space: nowrap;
  }
  .card-front .brand-name {
    left: 40px;
    top: 112px;
    font-size: 26px;
    color: var(--white);
    display: flex;
    align-items: center;
    gap: 12px;
  }
  .brand-mark {
    width: 14px;
    height: 14px;
    background: var(--white);
  }
  .divider {
    position: absolute;
    left: 40px;
    top: 170px;
    width: 330px;
    height: 1px;
    background: var(--soft-white);
  }
  .person {
    position: absolute;
    right: 28px;
    top: 34px;
    text-align: right;
  }
  .person-name {
    font-weight: 700;
    font-size: 17px;
    margin: 0;
  }
  .person-role {
    font-weight: 300;
    font-size: 11px;
    margin: 2px 0 0;
    padding-top: 2px;
    border-top: 1px solid var(--soft-white);
    display: inline-block;
    padding-left: 40px;
  }
  .contact-list {
    position: absolute;
    left: 40px;
    top: 190px;
    margin: 0;
    padding: 0;
    list-style: none;
    font-size: 12.5px;
    font-weight: 400;
    line-height: 21px;
  }
  .contact-list li {
    display: flex;
    align-items: center;
    gap: 8px;
  }
  .contact-list svg {
    width: 10px;
    height: 10px;
    fill: var(--white);
  }
  .card-back .brand-name {
    left: 0;
    right: 0;
    top: 118px;
    text-align: center;
    font-size: 34px;
    color: var(--ink);
  }
</style>
</head>
<body>
<main class="canvas">

  <section class="card card-front" aria-label="Front of business card">
    <svg class="card-bands" viewBox="0 0 540 309" aria-hidden="true">
      <polygon points="380,260 540,260 540,309 372,309 372,270" fill="#ffffff"/>
    </svg>

    <div class="brand-name"><span class="brand-mark"></span>Thornvale Group</div>
    <div class="divider"></div>

    <div class="person">
      <p class="person-name">Peter Castrell</p>
      <p class="person-role">President</p>
    </div>

    <ul class="contact-list">
      <li>
        <svg viewBox="0 0 10 10"><path d="M2 0.5 L3.8 2.6 L2.9 3.6 Q4 5.9 6.4 7.1 L7.4 6.2 L9.5 8 L8.3 9.5 Q2.5 8.5 0.5 1.7 Z"/></svg>
        (555) 204-6391
      </li>
      <li>
        <svg viewBox="0 0 10 10"><path d="M0.5 2 H9.5 V8 H0.5 Z M1 2.4 L5 5.4 L9 2.4" fill="none" stroke="#fff" stroke-width="1"/></svg>
        pc@thornvalegroup.example
      </li>
      <li>
        <svg viewBox="0 0 10 10"><circle cx="5" cy="5" r="4.5"/></svg>
        www.thornvalegroup.example
      </li>
    </ul>
  </section>

  <section class="card card-back" aria-label="Back of business card">
    <svg class="card-bands" viewBox="0 0 540 309" aria-hidden="true">
      <rect x="0" y="262" width="540" height="47" fill="#6d7075"/>
      <polygon points="0,262 0,309 300,309 300,256 288,248 280,262" fill="#0d3a66"/>
    </svg>
    <div class="brand-name">Thornvale Group</div>
  </section>

</main>
</body>
</html>
```